Veterinary Pylon

My veterinary clinic is not clearly visible from the street and I want to place a Pylon next to my driveway. I want a modern, elegant straight Design, the Photo shows the sheduled place. One can see the clinic on our Homepage: www.tailbright-vethaus.at
The last pictures are examples for pylones I like

Target Market(s)

the passing cars often miss my entry...I want to show where to turn left

Colors
3276b5
33a6d7
00a990

Requirements
Must have
• High value, simple elegance, size: 250cm (high) x 100cm (width)
Nice to have
• Our Logo, arrow(?)

A special Text is not necessary but this will be an option:

Biegen sie hier ab und wir biegen es wieder hin!
Should not have
• Too much Color, the colors I have chosen are the possible colors but it‘s not necessary to use them.

```html
<!DOCTYPE html>
<html lang="de">
<head>
<meta charset="utf-8">
<title>Tailbright Vethaus – Pylon</title>
<link rel="stylesheet" href="https://fonts.googleapis.com/css2?family=Archivo+Black&display=swap">
<style>
  :root {
    --brand-navy: #134a94;
    --brand-sky: #2fbbe0;
    --arrow-start: #1c64a6;
    --faint-blue: #e5edf6;
    --paper: #ffffff;
  }
  html, body {
    margin: 0;
    padding: 0;
    width: 1200px;
    height: 3000px;
    overflow: hidden;
    background: var(--paper);
  }
  .pylon {
    position: relative;
    width: 1200px;
    height: 3000px;
    overflow: hidden;
    background: var(--paper);
    font-family: "Archivo Black", "Arial Black", sans-serif;
  }
  .clinic-name {
    position: absolute;
    left: 0;
    top: 560px;
    width: 1200px;
    text-align: center;
    color: var(--brand-navy);
    text-transform: uppercase;
    line-height: 1.05;
    margin: 0;
    font-weight: 400;
  }
  .clinic-name .name-main {
    display: block;
    font-size: 128px;
    letter-spacing: 2px;
  }
  .clinic-name .name-sub {
    display: block;
    font-size: 84px;
    letter-spacing: 28px;
    margin-top: 24px;
    padding-left: 28px;
  }
  .turn-arrow {
    position: absolute;
    left: 0;
    top: 0;
  }
  .faint-name {
    position: absolute;
    left: 140px;
    top: 2380px;
    color: var(--faint-blue);
    font-size: 230px;
    line-height: 1;
    text-transform: uppercase;
    white-space: nowrap;
    margin: 0;
    font-weight: 400;
  }
  .faint-name span { display: block; }
</style>
</head>
<body>
  <main class="pylon">
    <h1 class="clinic-name">
      <span class="name-main">Tailbright</span>
      <span class="name-sub">Vethaus</span>
    </h1>

    <svg class="turn-arrow" width="1200" height="3000" viewBox="0 0 1200 3000" aria-label="Pfeil nach links – hier abbiegen" role="img">
      <defs>
        <linearGradient id="arrowGradient" x1="409" y1="0" x2="845" y2="0" gradientUnits="userSpaceOnUse">
          <stop offset="0" stop-color="var(--arrow-start)"/>
          <stop offset="1" stop-color="var(--brand-sky)"/>
        </linearGradient>
      </defs>
      <polygon fill="url(#arrowGradient)"
        points="409,1656 579,1486 579,1543 481,1639 845,1639 845,1673 481,1673 579,1771 579,1826"/>
    </svg>

    <p class="faint-name" aria-hidden="true">
      <span>Tailbright</span>
      <span>Vethaus</span>
    </p>
  </main>
</body>
</html>
```